Small corporate website template design

I need a couple templates designed for a small corporate website. The corporate site reflects the existence of the parent company which will own various brands/services that have their own websites, so it will mainly be used to present who we are, what we do, what is happening (news/events), how to contact us, link off to our other brand/service sites, as well as post information for public relations, investors, and job opportunities.

The company name is Brelvanto LLC (www.brelvanto-example.com), and the name is representative of stratified layers of interconnected digital services. The corporate site is not expected to generate a bunch of fanfare - that honor will be reserved for the externally linked brand/service sites.

The provided logo may be manipulated in color, size, shape, positioning, etc. to get it to fit with the design, but should be integrated in some way.

What we are looking for is a home page layout as well as a template for an inner page whereby the navigation/logo, etc may be diminished to some extent for the inner pages. We are also interested in reusable elements such as dividers, content containers, etc. in order to represent the types of information described above that we would like to present as described above.

We are particularly interested in consistency of design elements, conservative use of color (including consideration of accessibility concerns), judicious use of whitespace in favor of simplified messaging, and something lending itself well to internationalization/translation.

Target Market(s)

Small business owners, entrepreneurs (B2B)

Number of Pages Required

2 page

Font styles to use
Sans Serif

Requirements
Must have
• See the attached PDF with the logo concept, color swatches, and comparative sites.

```html
<!DOCTYPE html>
<html lang="en">
<head>
<meta charset="utf-8">
<title>Brelvanto LLC</title>
<link href="https://fonts.googleapis.com/css2?family=Roboto+Slab:wght@400&family=Arimo:wght@400&family=Montserrat:wght@500&display=swap" rel="stylesheet">
<style>
  :root {
    --orange: #f7941d;
    --navy: #2a5389;
    --heading: #2d5a8e;
    --text: #444a52;
    --white: #ffffff;
    --sand: #fdf5e9;
    --peach: #fde4c4;
    --footer: #2b5593;
    --hero-light: #dfeaf4;
    --hero-dark: #4f7fae;
  }
  * { box-sizing: border-box; margin: 0; padding: 0; }
  html, body { width: 736px; height: 1200px; overflow: hidden; background: var(--white); }
  body { position: relative; font-family: "Arimo", Arial, sans-serif; color: var(--text); }
  h1, h2 { font-weight: 400; }
  .abs { position: absolute; }

  /* header */
  .site-header { position: absolute; left: 0; top: 0; width: 736px; height: 66px; background: var(--white); }
  .brand { position: absolute; left: 53px; top: 16px; display: flex; align-items: center; gap: 7px; }
  .brand-mark { width: 26px; height: 26px; background: #1b1b1b; }
  .brand-name { font-family: "Roboto Slab", Georgia, serif; font-weight: 400; font-size: 17px; color: var(--orange); }
  .main-nav { position: absolute; top: 28px; left: 0; width: 736px; font-family: "Roboto Slab", Georgia, serif; font-weight: 400; font-size: 7.5px; color: #333; }
  .main-nav span { position: absolute; white-space: nowrap; }
  .main-nav .is-active { color: var(--orange); }

  /* hero */
  .hero { position: absolute; left: 0; top: 66px; width: 736px; height: 314px;
    background: radial-gradient(ellipse at 35% 35%, var(--hero-light) 0%, #a9c3dc 45%, var(--hero-dark) 100%); }
  .hero-title { position: absolute; left: 466px; top: 152px; font-family: "Roboto Slab", Georgia, serif; font-size: 28px; color: var(--heading); white-space: nowrap; }
  .hero-text { position: absolute; left: 467px; top: 190px; width: 215px; font-size: 7.3px; line-height: 17.5px; color: var(--white); }
  .btn { position: absolute; background: var(--orange); color: var(--white); display: flex; align-items: center; justify-content: center; border-radius: 2px; white-space: nowrap; }
  .btn-hero { left: 468px; top: 257px; width: 75px; height: 26px; font-family: "Roboto Slab", Georgia, serif; font-size: 10.5px; }
  .btn-small { width: 70px; height: 26px; font-family: "Roboto Slab", Georgia, serif; font-size: 7.5px; }

  /* sections */
  .section-title { position: absolute; font-family: "Roboto Slab", Georgia, serif; font-size: 20px; color: var(--heading); white-space: nowrap; }
  .body-copy { position: absolute; font-size: 7px; line-height: 17.5px; color: var(--text); }
  .check-list { position: absolute; list-style: none; font-size: 7px; color: var(--text); }
  .check-list li { height: 21px; display: flex; align-items: center; gap: 7px; white-space: nowrap; }

  /* footer */
  .site-footer { position: absolute; left: 0; top: 1072px; width: 736px; height: 128px; background: var(--footer); color: var(--white); }
  .contact-item { position: absolute; top: 18px; display: flex; gap: 10px; }
  .contact-icon { width: 32px; height: 32px; border: 1px solid var(--white); border-radius: 50%; display: flex; align-items: center; justify-content: center; flex-shrink: 0; }
  .contact-label { font-family: "Montserrat", Arial, sans-serif; font-weight: 500; font-size: 11px; margin-top: 2px; }
  .contact-value { font-size: 7.3px; line-height: 13px; margin-top: 2px; white-space: nowrap; }
  .footer-rule { position: absolute; left: 53px; top: 77px; width: 630px; height: 1px; background: rgba(255,255,255,0.15); }
  .copyright { position: absolute; left: 53px; top: 99px; font-size: 7.3px; white-space: nowrap; }
  .social { position: absolute; top: 92px; width: 22px; height: 22px; border: 1px solid var(--white); border-radius: 50%; }
</style>
</head>
<body>

<header class="site-header">
  <div class="brand"><span class="brand-mark"></span><span class="brand-name">Brelvanto</span></div>
  <nav class="main-nav">
    <span class="is-active" style="left:288px">HOME</span>
    <span style="left:345px">ABOUT US</span>
    <span style="left:417px">HOW WE ARE</span>
    <span style="left:500px">WHAT WE DO</span>
    <span style="left:582px">BLOG</span>
    <span style="left:637px">CONTACT US</span>
  </nav>
</header>

<section class="hero" role="img" aria-label="Glossy blue molecule structure photo">
  <h1 class="hero-title">Brelvanto</h1>
  <p class="hero-text">Sed ut perspiciatis unde omnis iste natus error sit voluptatem accusantium doloremque laudantium, totam rem aperiam, eaq ue ipsa quae ab vitae dicta sunt explicabo.</p>
  <span class="btn btn-hero">Read More</span>
</section>

<svg class="abs" style="left:0;top:380px" width="736" height="692" viewBox="0 380 736 692">
  <polygon points="0,380 30,376 172,440 120,600 0,630" fill="var(--sand)"/>
  <polygon points="560,421 720,431 780,560 680,726 520,704 458,550" fill="#5d7088" role="img" aria-label="Photo of a hand touching a glowing network of connected points"/>
  <polygon points="0,732 186,732 263,874 186,1016 0,1016" fill="#3f434b" role="img" aria-label="Photo of a hand touching a network of connected people figures"/>
  <polygon points="549,970 571,970 580,987 571,1004 549,1004 540,987" fill="var(--peach)"/>
  <polygon points="586,983 635,983 656,1021 635,1059 586,1059 568,1021" fill="var(--peach)"/>
</svg>

<section class="who-we-are">
  <h2 class="section-title" style="left:78px;top:449px">Who We Are</h2>
  <p class="body-copy" style="left:78px;top:493px;width:320px">Sed ut perspiciatis unde omnis iste natus error sit voluptatem accusantium doloremque lau-dantium, totam rem aperiam, eaque ipsa quae ab illo inventore veritatis et quasi architecto beatae vitae dicta sunt explicabo. Nemo enim ipsam voluptatem quia voluptas sit aspernatur aut odit magni dolores eos qui ratione voluptatem sequi nesciunt.</p>
  <p class="body-copy" style="left:78px;top:575px;width:320px">Nemo enim ipsam voluptatem quia voluptas sit aspernatur aut odit aut fugit, sed quia conse-quuntur magni dolores eos qui ratione voluptatem sequi nesciunt. Neque porro quisquam est, qui dolorem ipsum quia dolor sit amet, consectetur, adipisci velit, sed quia</p>
  <span class="btn btn-small" style="left:79px;top:647px">RAED MORE</span>
</section>

<section class="what-we-do">
  <h2 class="section-title" style="left:324px;top:750px">What We Do</h2>
  <p class="body-copy" style="left:325px;top:794px;width:310px">Sed ut perspiciatis unde omnis iste natus error sit voluptatem accusantium doloremque lau-dantium, totam rem aperiam, eaque ipsa quae ab illo inventore veritatis et quasi architecto beatae vitae dicta sunt explicabo.</p>
  <ul class="check-list" style="left:327px;top:850px">
    <li><svg width="7" height="6" viewBox="0 0 7 6"><path d="M0.5 3 L2.6 5 L6.5 0.8" fill="none" stroke="var(--navy)" stroke-width="1.5"/></svg>Nemo enim ipsam voluptatem quia voluptas</li>
    <li><svg width="7" height="6" viewBox="0 0 7 6"><path d="M0.5 3 L2.6 5 L6.5 0.8" fill="none" stroke="var(--navy)" stroke-width="1.5"/></svg>sit aspernatur aut odit aut fugit, sed quia consequuntur</li>
    <li><svg width="7" height="6" viewBox="0 0 7 6"><path d="M0.5 3 L2.6 5 L6.5 0.8" fill="none" stroke="var(--navy)" stroke-width="1.5"/></svg>magni dolores eos qui ratione voluptatem sequi nesciunt.</li>
    <li><svg width="7" height="6" viewBox="0 0 7 6"><path d="M0.5 3 L2.6 5 L6.5 0.8" fill="none" stroke="var(--navy)" stroke-width="1.5"/></svg>Neque porro quisquam est, qui dolorem ipsum quia dolor</li>
  </ul>
  <span class="btn btn-small" style="left:326px;top:948px">RAED MORE</span>
</section>

<footer class="site-footer">
  <div class="contact-item" style="left:74px">
    <span class="contact-icon"><svg width="10" height="12" viewBox="0 0 10 12"><path d="M5 0.5 A4 4 0 0 1 9 4.5 C9 7.5 5 11.5 5 11.5 C5 11.5 1 7.5 1 4.5 A4 4 0 0 1 5 0.5 Z" fill="var(--white)"/><circle cx="5" cy="4.5" r="1.5" fill="var(--footer)"/></svg></span>
    <div><div class="contact-label">Address :</div><div class="contact-value"># 2152 Lorem Ipsum DUmmy Text<br>Lorem Ipsum Dummy</div></div>
  </div>
  <div class="contact-item" style="left:316px">
    <span class="contact-icon"><svg width="12" height="9" viewBox="0 0 12 9"><rect x="0.6" y="0.6" width="10.8" height="7.8" fill="none" stroke="var(--white)" stroke-width="1.2"/><path d="M0.6 0.6 L6 5 L11.4 0.6" fill="none" stroke="var(--white)" stroke-width="1.2"/></svg></span>
    <div><div class="contact-label">Email</div><div class="contact-value">info@brelvanto-example.com</div></div>
  </div>
  <div class="contact-item" style="left:532px">
    <span class="contact-icon"><svg width="10" height="10" viewBox="0 0 10 10"><path d="M2 0.5 L3.8 2.8 L2.8 4 C3.5 5.5 4.5 6.5 6 7.2 L7.2 6.2 L9.5 8 L8.3 9.5 C4 9 1 6 0.5 1.7 Z" fill="var(--white)"/></svg></span>
    <div><div class="contact-label">Phone</div><div class="contact-value">Mobile : (000)-555-0147</div></div>
  </div>
  <div class="footer-rule"></div>
  <p class="copyright">© Copyright-2018 Brelvanto.All rights reserved</p>
  <span class="social" style="left:635px"></span>
  <span class="social" style="left:661px"></span>
</footer>

</body>
</html>
```